K7 Services business card design contest. Use logo and create a professional layout.

See attached sample. Please sharpen all text and images, don't want any pix-elated content. We are looking for a clean look that quickly provides the information need. Please include our information provided on the sample card. Please feel free to offer any design changes. Please only user the colors provided: #2D3539 & #FFA500. Do not prefer any images other than the K7 Logo

Target Market(s)

Construction, Architects, General Contractors, residential

Industry/Entity Type

Business

Contact Information for Business Card

Company logo, Name, email, fax & phone

Font styles to use
Other font styles liked:
• Josefin Slab

Requirements
Must have
• Name
• Phone & Fax #'s
• address
• Logo
• Website url: www.kq7services.example
Nice to have
• Font Colors #2D3539 & #FFA400
• We prefer a white background.

```html
<!DOCTYPE html>
<html lang="en">
<head>
<meta charset="utf-8">
<title>K7 Services Business Card</title>
<link href="https://fonts.googleapis.com/css2?family=Montserrat:wght@400;500;600&display=swap" rel="stylesheet">
<style>
  :root {
    --ink: #2D3539;
    --accent: #F0982A;
    --paper: #FFFFFF;
    --backdrop: #E3E3E3;
  }
  * { margin: 0; padding: 0; box-sizing: border-box; }
  html, body {
    width: 1200px; height: 852px; overflow: hidden;
    background: var(--backdrop);
    font-family: "Montserrat", sans-serif;
    color: var(--ink);
  }
  .stage { position: relative; width: 1200px; height: 852px; }
  .card {
    position: absolute; width: 520px; height: 297px;
    background: var(--paper); border-radius: 14px; overflow: hidden;
    box-shadow: 0 6px 18px rgba(0,0,0,0.18);
  }
  .card--front { left: 70px; top: 140px; }
  .card--back { left: 610px; top: 410px; }

  .company-name {
    position: absolute; line-height: 1; white-space: nowrap;
    font-weight: 600; color: var(--ink);
  }
  .card--front .company-name {
    left: 50%; top: 50%; transform: translate(-50%, -50%);
    font-size: 40px;
  }
  .card--back .company-name { left: 36px; top: 84px; font-size: 26px; }

  .person { position: absolute; right: 34px; top: 34px; text-align: right; }
  .person__name { font-size: 17px; color: var(--accent); font-weight: 400; }
  .person__title { font-size: 11px; margin-top: 2px; }

  .divider {
    position: absolute; left: 36px; top: 150px; width: 250px; height: 1.5px;
    background: var(--accent);
  }

  .contact { position: absolute; right: 24px; top: 86px; list-style: none; }
  .contact__item {
    display: flex; align-items: center; justify-content: flex-end; gap: 8px;
    font-size: 11px; height: 18px;
  }
  .contact__icon { width: 11px; height: 11px; fill: var(--accent); }

  .address {
    position: absolute; left: 36px; top: 170px;
    font-size: 11px; line-height: 1.5; font-style: normal;
  }

  .band {
    position: absolute; left: 0; right: 0; bottom: 0; height: 78px;
    background: var(--accent);
  }
  .band__services {
    position: absolute; right: 24px; top: 12px;
    color: var(--paper); font-size: 11.5px; letter-spacing: 0.6px;
  }
</style>
</head>
<body>
<main class="stage">
  <section class="card card--front" aria-label="Card front">
    <div class="company-name">K7 Services</div>
  </section>

  <section class="card card--back" aria-label="Card back">
    <div class="company-name">K7 Services</div>

    <div class="person">
      <div class="person__name">Daniel R. Hollis, MBA</div>
      <div class="person__title">Director of Operations</div>
    </div>

    <div class="divider"></div>

    <ul class="contact">
      <li class="contact__item">(555) 014 - 2071
        <svg class="contact__icon" viewBox="0 0 12 12" aria-hidden="true"><path d="M1 4c0-2 2-3 5-3s5 1 5 3l-2 1-1-1H4L3 5 1 4zm2 2h6l1 5H2l1-5z"/></svg>
      </li>
      <li class="contact__item">(555) 018 - 3094
        <svg class="contact__icon" viewBox="0 0 12 12" aria-hidden="true"><path d="M3 1h6v3H3zM1 5h10v6H1zm2 2v1h2V7zm4 0v1h2V7z"/></svg>
      </li>
      <li class="contact__item">www.kq7services.example
        <svg class="contact__icon" viewBox="0 0 12 12" aria-hidden="true"><circle cx="6" cy="6" r="5"/><path d="M1 6h10M6 1v10" stroke="#fff" stroke-width="0.8"/></svg>
      </li>
    </ul>

    <address class="address">
      1280 Ridgeline Road, Suite<br>
      410-215 Maple Falls, Ohio, 40000
    </address>

    <div class="band">
      <div class="band__services">DRONE | WEBCAM | VIDEO</div>
    </div>
  </section>
</main>
</body>
</html>
```